Business card design for modern PanoWalk agency

Hello,

I need a business card design for my company Kites7Market.
We mainly offer Zorvex PanoWalk Tours (360° Photography) and it should be a business card with following details:

Name: Tobias Wendler
Number: +49 176 58 20 917
Mail: tobias@kites7market.com
website: kites7market.com

Main colour that we use is the red of the logo.
It´s also important to integrate the "Zorvex Verified logo" as the person on this business card is a Zorvex verified photographer.

And if possible we would also like to integrate something like send us a sms or whatsapp and we call you back. As the number is german but we sell now in Vienna, Austria.

We offer a good price but very high photography quality, as we are mostly students - that´s our concept.

Maybe an idea is to integrate something 360° on the back-side of the card, for example the photo attached (just an idea) or some great design.
See flyer (attached) and kites7market.com for inspiration, maybe use of the photo of me (attached) in a circle or something

I´m very excited for your designs and thanks a lot in advance!! :)

Target Market(s)

Shops, hotels, shopping centers, etc. in Vienna, Austria

Industry/Entity Type

Business

Contact Information for Business Card

double-sided, use red of the logo, 360° zorvex pano walk certified photographer

Font styles to use
Serif
Sans Serif

Colors
ec1f27

Requirements
Nice to have
• maybe some 360° design on back-side
• maybe include photo of me in a circle or something or sketched in red colour

```html
<!DOCTYPE html>
<html lang="en">
<head>
<meta charset="utf-8">
<title>Kites7Market business card</title>
<link rel="stylesheet" href="https://fonts.googleapis.com/css2?family=Arvo:wght@700&family=Montserrat:wght@400;500;600&display=swap">
<style>
  :root {
    --brand-red: #ec1f27;
    --ink: #3a3a3a;
    --ink-soft: #5a5a5a;
    --paper: #ffffff;
    --backdrop: #e4e4e4;
    --band-blue: #4a86e8;
    --band-green: #34a853;
    --band-yellow: #f6b91a;
    --badge-green: #34a853;
  }
  * { box-sizing: border-box; margin: 0; padding: 0; }
  html, body { width: 1200px; height: 726px; overflow: hidden; }
  body {
    background: var(--backdrop);
    font-family: "Montserrat", Arial, sans-serif;
    color: var(--ink);
    position: relative;
  }
  .card {
    position: absolute;
    top: 213px;
    width: 520px;
    height: 300px;
    background: var(--paper);
    overflow: hidden;
  }
  .card--front { left: 45px; }
  .card--back { left: 635px; }

  /* front */
  .verified-badge {
    position: absolute;
    display: flex;
    align-items: center;
    gap: 6px;
  }
  .verified-badge__plate {
    width: 86px; height: 14px; border-radius: 3px; background: #c9c9c9;
  }
  .verified-badge__tick {
    width: 16px; height: 16px; border-radius: 50%; background: var(--badge-green);
  }
  .card--front .verified-badge { top: 10px; right: 16px; }
  .tour-photo {
    position: absolute;
    left: 0; right: 0; top: 36px; height: 188px;
    background: linear-gradient(135deg, #b9b2a6 0%, #8f8a80 35%, #c7b39a 60%, #7d8791 100%);
  }
  .web-line {
    position: absolute;
    top: 238px; left: 0; right: 0;
    text-align: center;
    font-size: 13px;
    font-weight: 500;
    color: var(--ink);
  }
  .web-line__domain { color: var(--brand-red); }
  .colour-bands {
    position: absolute;
    left: 0; right: 0; bottom: 0; height: 10px;
    display: flex;
  }
  .colour-bands span { flex: 1; }
  .band--red { background: var(--brand-red); }
  .band--blue { background: var(--band-blue); }
  .band--green { background: var(--band-green); }
  .band--yellow { background: var(--band-yellow); }

  /* back */
  .company-mark {
    position: absolute;
    top: 30px; right: 28px;
    display: flex; align-items: center; gap: 10px;
  }
  .company-mark__square {
    width: 48px; height: 36px; background: var(--brand-red);
  }
  .company-mark__name {
    font-size: 21px; font-weight: 600; color: var(--ink-soft);
  }
  .person {
    position: absolute; top: 112px; left: 30px;
  }
  .person__name {
    font-family: "Arvo", Georgia, serif;
    font-weight: 700;
    font-size: 27px;
    color: var(--brand-red);
  }
  .person__role {
    margin-top: 4px;
    font-size: 11px;
    line-height: 1.35;
    color: var(--ink);
    font-weight: 500;
  }
  .card--back .verified-badge { top: 172px; right: 28px; }
  .contact-list {
    position: absolute; left: 30px; bottom: 26px;
    list-style: none;
    font-size: 13px;
    line-height: 1.55;
    color: var(--ink);
  }
  .contact-list li { display: flex; align-items: center; gap: 10px; }
  .contact-list svg { width: 12px; height: 12px; fill: var(--brand-red); flex: none; }
</style>
</head>
<body>
  <section class="card card--front" aria-label="Card front">
    <div class="verified-badge" aria-label="Zorvex verified badge">
      <span class="verified-badge__plate"></span>
      <span class="verified-badge__tick"></span>
    </div>
    <div class="tour-photo" role="img" aria-label="360° panorama photo of a shopping centre interior with escalators"></div>
    <p class="web-line">www.<span class="web-line__domain">kites7market</span>.com</p>
    <div class="colour-bands">
      <span class="band--red"></span><span class="band--blue"></span><span class="band--green"></span><span class="band--yellow"></span>
    </div>
  </section>

  <section class="card card--back" aria-label="Card back">
    <div class="company-mark">
      <span class="company-mark__square"></span>
      <span class="company-mark__name">Kites7Market</span>
    </div>
    <div class="person">
      <h1 class="person__name">Tobias Wendler</h1>
      <p class="person__role">360° zorvex pano walk<br>certified photographer</p>
    </div>
    <div class="verified-badge" aria-label="Zorvex verified badge">
      <span class="verified-badge__plate"></span>
      <span class="verified-badge__tick"></span>
    </div>
    <ul class="contact-list">
      <li>
        <svg viewBox="0 0 24 24" aria-hidden="true"><path d="M6.6 10.8a15.1 15.1 0 0 0 6.6 6.6l2.2-2.2a1 1 0 0 1 1-.25 11.4 11.4 0 0 0 3.6.57 1 1 0 0 1 1 1V20a1 1 0 0 1-1 1A17 17 0 0 1 3 4a1 1 0 0 1 1-1h3.5a1 1 0 0 1 1 1c0 1.25.2 2.45.57 3.57a1 1 0 0 1-.25 1z"/></svg>
        +49 176 58 20 917
      </li>
      <li>
        <svg viewBox="0 0 24 24" aria-hidden="true"><path d="M2 5h20v14H2z M4 7v.5l8 5 8-5V7l-8 5z" fill-rule="evenodd"/></svg>
        tobias@kites7market.com
      </li>
      <li>
        <svg viewBox="0 0 24 24" aria-hidden="true"><path d="M12 2a10 10 0 1 0 0 20 10 10 0 0 0 0-20zm6.9 9h-3a15 15 0 0 0-1.3-5.6A8 8 0 0 1 18.9 11zM12 4.1c.9 1.2 1.7 3.7 1.9 6.9h-3.8c.2-3.2 1-5.7 1.9-6.9zM9.4 5.4A15 15 0 0 0 8.1 11h-3a8 8 0 0 1 4.3-5.6zM5.1 13h3a15 15 0 0 0 1.3 5.6A8 8 0 0 1 5.1 13zm6.9 6.9c-.9-1.2-1.7-3.7-1.9-6.9h3.8c-.2 3.2-1 5.7-1.9 6.9zm2.6-1.3a15 15 0 0 0 1.3-5.6h3a8 8 0 0 1-4.3 5.6z"/></svg>
        www.kites7market.com
      </li>
    </ul>
  </section>
</body>
</html>
```